Jolly Hounds Dog Behaviour, Training and Natural Healthcare Business Card Design

I am an experienced and qualified dog behavioural trainer and natural animal healthcare consultant offering a range of services to help pet dog owners with the "whole dog".
COLOURS: A soft light blue in the background - can be fading out or split, red should also feature
LOGO: Dog, healing hands, silhouette, shadow
SERVICES: Behaviour Consults, Training, Complex Skills Coaching Walking Coaching, Diet & Nutrition, Environmental Enrichment, Lifestyle and Lifestage Adaptations, Massage, Natural Health Options
BY LINE: Happy Dogs, Happy Owners
VALUES: Promoting communication and connection between dogs and their owners.
FOCUS: Nutritional guidance and environmental adaptation are often needed to complete the package and increase the success rate of training and behaviour modification.

Target Market(s)

Everyone who has a dog who they wish to improve their relationship with

Industry/Entity Type

Communication

Contact Information for Business Card

Jolly Hounds, Rebecca Thornbury, 0427 861350, jollyhounds7@fernpost.example, www.jollyhounds7.example, Qualified Dog Behavioural Trainer and Natural Animal Healthcare Consultant

Font styles to use
Sans Serif
Script

Colors
85cae6
ec2027

Requirements
Must have
• A clear indication that it is a dog services business. A raised feature
Should not have
• Pawprints, cartoons

```html
<!DOCTYPE html>
<html lang="en">
<head>
<meta charset="utf-8">
<title>Jolly Hounds – Business Card</title>
<link rel="stylesheet" href="https://fonts.googleapis.com/css2?family=Ubuntu:wght@500;700&family=Ubuntu+Condensed&display=swap">
<style>
  :root {
    --page-bg: #2a2a2a;
    --brand-red: #ec2027;
    --brand-blue: #85cae6;
    --grass-dark: #3f6a2c;
    --grass-mid: #6a9a45;
    --grass-light: #9cbf74;
    --band-shade: rgba(70, 70, 70, 0.62);
    --ink-light: #ffffff;
  }
  html, body {
    margin: 0;
    width: 1200px;
    height: 900px;
    overflow: hidden;
    background: var(--page-bg);
  }
  .business-card {
    position: absolute;
    left: 100px;
    top: 164px;
    width: 1000px;
    height: 572px;
    overflow: hidden;
    box-shadow: 0 18px 40px rgba(0,0,0,0.55);
  }
  .card-art {
    position: absolute;
    inset: 0;
    width: 100%;
    height: 100%;
  }
  .brand-band {
    position: absolute;
    left: 300px;
    top: 18px;
    width: 560px;
    height: 132px;
    background: var(--band-shade);
    color: var(--ink-light);
    text-align: center;
    font-family: "Ubuntu", sans-serif;
  }
  .brand-name {
    margin: 10px 0 4px;
    font-size: 62px;
    font-weight: 700;
    line-height: 1;
  }
  .brand-tagline {
    margin: 0;
    font-size: 19px;
    font-weight: 500;
    line-height: 1.2;
  }
  .contact-person {
    position: absolute;
    left: 590px;
    top: 360px;
    color: var(--ink-light);
  }
  .person-name {
    margin: 0;
    font-family: "Ubuntu Condensed", sans-serif;
    font-size: 46px;
    line-height: 1.05;
  }
  .person-phone {
    margin: 0;
    font-family: "Ubuntu", sans-serif;
    font-weight: 500;
    font-size: 30px;
    line-height: 1.2;
  }
  .contact-line {
    position: absolute;
    top: 498px;
    display: flex;
    align-items: center;
    gap: 14px;
    color: var(--ink-light);
    font-family: "Ubuntu", sans-serif;
    font-weight: 500;
    font-size: 24px;
  }
  .contact-line--email { left: 60px; }
  .contact-line--web { left: 560px; }
  .contact-icon { width: 22px; height: 22px; flex: none; }
</style>
</head>
<body>
  <section class="business-card">
    <svg class="card-art" viewBox="0 0 1000 572" preserveAspectRatio="none">
      <defs>
        <radialGradient id="grassTone" cx="40%" cy="45%" r="75%">
          <stop offset="0" stop-color="var(--grass-light)"/>
          <stop offset="0.55" stop-color="var(--grass-mid)"/>
          <stop offset="1" stop-color="var(--grass-dark)"/>
        </radialGradient>
      </defs>
      <rect class="photo-area" role="img" aria-label="Photo of a fluffy white puppy running on green grass with a toy in its mouth" x="0" y="0" width="1000" height="572" fill="url(#grassTone)"/>
      <path class="swoosh-blue" d="M0 328 Q 560 250 1000 52 L1000 150 Q 520 310 0 330 Z" fill="var(--brand-blue)"/>
      <path class="swoosh-edge" d="M0 328 Q 560 250 1000 52" fill="none" stroke="#ffffff" stroke-width="3"/>
      <path class="panel-red" d="M0 330 Q 520 310 1000 150 L1000 572 L0 572 Z" fill="var(--brand-red)"/>
    </svg>

    <header class="brand-band">
      <h1 class="brand-name">Jolly Hounds</h1>
      <p class="brand-tagline">Qualified Dog Behavioural<br>Trainer and Natural Animal Healthcare Consultant</p>
    </header>

    <div class="contact-person">
      <p class="person-name">Rebecca Thornbury</p>
      <p class="person-phone">0427 861350</p>
    </div>

    <div class="contact-line contact-line--email">
      <svg class="contact-icon" viewBox="0 0 22 22" aria-hidden="true">
        <rect x="2" y="5" width="18" height="12" rx="1.5" fill="#ffffff"/>
        <path d="M2.5 5.5 L11 12 L19.5 5.5" fill="none" stroke="var(--brand-red)" stroke-width="1.6"/>
      </svg>
      <span>jollyhounds7@fernpost.example</span>
    </div>

    <div class="contact-line contact-line--web">
      <svg class="contact-icon" viewBox="0 0 22 22" aria-hidden="true">
        <circle cx="11" cy="11" r="9" fill="none" stroke="#ffffff" stroke-width="1.8"/>
        <ellipse cx="11" cy="11" rx="4" ry="9" fill="none" stroke="#ffffff" stroke-width="1.4"/>
        <line x1="2" y1="11" x2="20" y2="11" stroke="#ffffff" stroke-width="1.4"/>
      </svg>
      <span>www.jollyhounds7.example</span>
    </div>
  </section>
</body>
</html>
```